Business Card for my New Brokerage

Looking to get a business card design for my new Real Estate Brokerage.
I want it with Picture, Phone Number, Email, Website, Office Address
Name and Designation. Please add logo too.

Target Market(s)

Real Estate Investors or Home Buyers

Industry/Entity Type

Real Estate

Contact Information for Business Card

Name, Email, Phone Number, website, email, office address

Colors
EB3D1F
EC4F4E
F09395
F8D3D4
FCEDEE

Requirements
Must have
• Minimalistic, Clean, Modern, Photo
Nice to have
• White and Red Colors

```html
<!DOCTYPE html>
<html lang="en">
<head>
<meta charset="utf-8">
<title>Ember Realty Inc – Business Card</title>
<link rel="stylesheet" href="https://fonts.googleapis.com/css2?family=Lato:wght@400;700;900&display=swap">
<style>
  :root {
    --brand-red: #dc0000;
    --paper: #ffffff;
    --gold: #d8b45a;
    --gold-light: #f3dc8e;
    --backdrop: #2b2b2b;
    --photo-light: #f4f4f4;
    --photo-mid: #d9d4cf;
    --photo-dark: #3a3a3a;
  }
  * { margin: 0; padding: 0; box-sizing: border-box; }
  html, body { width: 1200px; height: 1015px; overflow: hidden; }
  body {
    background: var(--backdrop);
    font-family: "Lato", sans-serif;
    display: flex;
    flex-direction: column;
    align-items: center;
    justify-content: center;
    gap: 60px;
  }
  .card {
    position: relative;
    width: 640px;
    height: 366px;
    overflow: hidden;
    box-shadow: 0 12px 30px rgba(0,0,0,0.5);
  }
  /* Front */
  .card-front {
    background: var(--paper);
    display: flex;
    align-items: center;
    justify-content: center;
  }
  .wordmark { display: flex; flex-direction: column; align-items: center; }
  .wordmark-row { display: flex; align-items: center; gap: 12px; }
  .wordmark-name {
    color: var(--brand-red);
    font-weight: 900;
    font-size: 84px;
    letter-spacing: 2px;
    line-height: 1;
  }
  .wordmark-dot {
    width: 14px; height: 14px;
    background: var(--brand-red);
  }
  .wordmark-tagline {
    color: var(--brand-red);
    font-weight: 400;
    font-size: 22px;
    letter-spacing: 14px;
    margin-top: 10px;
    padding-left: 14px;
  }
  /* Back */
  .card-back { background: var(--brand-red); }
  .card-back .backdrop { position: absolute; inset: 0; display: block; }
  .contact {
    position: absolute;
    left: 48px;
    top: 70px;
    color: var(--paper);
  }
  .person-name {
    font-weight: 900;
    font-size: 26px;
    letter-spacing: 1px;
    text-transform: uppercase;
  }
  .person-title { font-size: 18px; margin-top: 2px; }
  .address { margin-top: 70px; font-size: 18px; line-height: 1.3; }
  .contact-list { list-style: none; margin-top: 18px; font-size: 18px; line-height: 1.45; }
  .contact-list li { display: flex; align-items: center; gap: 10px; }
  .contact-list svg { width: 18px; height: 18px; flex: none; }
</style>
</head>
<body>

  <section class="card card-front" aria-label="Card front">
    <div class="wordmark">
      <div class="wordmark-row">
        <span class="wordmark-name">EMBER</span>
        <span class="wordmark-dot"></span>
      </div>
      <span class="wordmark-tagline">REALTY INC</span>
    </div>
  </section>

  <section class="card card-back" aria-label="Card back">
    <svg class="backdrop" viewBox="0 0 640 366" width="640" height="366">
      <defs>
        <linearGradient id="gold-arc" x1="0" y1="0" x2="1" y2="1">
          <stop offset="0" stop-color="var(--gold-light)"/>
          <stop offset="1" stop-color="var(--gold)"/>
        </linearGradient>
        <linearGradient id="portrait-tones" x1="0" y1="0" x2="0" y2="1">
          <stop offset="0" stop-color="var(--photo-light)"/>
          <stop offset="0.5" stop-color="var(--photo-mid)"/>
          <stop offset="1" stop-color="var(--photo-dark)"/>
        </linearGradient>
      </defs>
      <circle class="photo-frame" cx="520" cy="40" r="270" fill="var(--paper)"/>
      <g role="img" aria-label="Portrait photo of the managing director in a dark suit">
        <circle cx="520" cy="40" r="250" fill="url(#portrait-tones)"/>
      </g>
      <path class="gold-ring" d="M 268 -4 A 256 256 0 0 0 498 295" fill="none" stroke="url(#gold-arc)" stroke-width="4"/>
    </svg>

    <div class="contact">
      <h1 class="person-name">Daniel Hayes</h1>
      <p class="person-title">Managing Director</p>
      <p class="address">18, Harbor View Lane<br>Brookfield, 30418</p>
      <ul class="contact-list">
        <li>
          <svg viewBox="0 0 24 24" aria-hidden="true"><path fill="#fff" d="M6.6 10.8a15.1 15.1 0 0 0 6.6 6.6l2.2-2.2a1 1 0 0 1 1-.25 11.4 11.4 0 0 0 3.6.57 1 1 0 0 1 1 1V20a1 1 0 0 1-1 1A17 17 0 0 1 3 4a1 1 0 0 1 1-1h3.5a1 1 0 0 1 1 1c0 1.25.2 2.450.57 3.57a1 1 0 0 1-.25 1z"/></svg>
          044-555 010 203
        </li>
        <li>
          <svg viewBox="0 0 24 24" aria-hidden="true"><rect x="2" y="5" width="20" height="14" fill="none" stroke="#fff" stroke-width="2"/><path d="M2 5l10 8 10-8" fill="none" stroke="#fff" stroke-width="2"/></svg>
          hello@emberrealty.com
        </li>
        <li>
          <svg viewBox="0 0 24 24" aria-hidden="true"><circle cx="12" cy="12" r="10" fill="none" stroke="#fff" stroke-width="2"/><path d="M2 12h20M12 2c3 3 3 17 0 20M12 2c-3 3-3 17 0 20" fill="none" stroke="#fff" stroke-width="1.6"/></svg>
          www.emberrealty.com
        </li>
      </ul>
    </div>
  </section>

</body>
</html>
```